Copperleaf Roofing Business Card

This is my current business card. But I’d like to make some changes. Somewhere on the card I’d like to list some of the services we offer. Maybe on the back? But I’d still like to keep the red. White and black modern look.

-residential & commercial roofing
-Roof Repairs & Maintenance
-Storm Damage & Insurance Claims specialist
-Christmas Lights and permanent Christmas lights
Fencing. Windows. Gutters. Siding. Sheetrock, painting.

```html
<!DOCTYPE html>
<html lang="en">
<head>
<meta charset="utf-8">
<title>Copperleaf Roofing Business Card</title>
<link href="https://fonts.googleapis.com/css2?family=Audiowide&family=Arimo:wght@400;700&display=swap" rel="stylesheet">
<style>
  :root {
    --stage: #2e2e2e;
    --paper: #ffffff;
    --paper-shade: #ececec;
    --ink: #111111;
    --body: #444444;
    --red: #d3141c;
    --red-dark: #8f0d12;
    --rule: #e8b4a8;
    --art-dark: #1a1a1a;
    --art-mid: #3a3a3a;
  }
  * { box-sizing: border-box; margin: 0; padding: 0; }
  html, body { width: 1200px; height: 900px; overflow: hidden; }
  body {
    background: var(--stage);
    font-family: "Arimo", Arial, sans-serif;
    position: relative;
  }
  .card {
    position: absolute;
    left: 250px;
    width: 700px;
    height: 400px;
    background: linear-gradient(135deg, var(--paper) 0%, var(--paper) 55%, var(--paper-shade) 100%);
    overflow: hidden;
    box-shadow: 0 10px 28px rgba(0,0,0,.45);
  }
  .card--back { top: 40px; }
  .card--front { top: 460px; }

  .tartan-band {
    position: absolute;
    left: 0; right: 0; bottom: 0;
    height: 26px;
    background: linear-gradient(180deg, var(--red) 0%, var(--red-dark) 100%);
  }

  .brand-art {
    position: absolute;
    background: linear-gradient(160deg, var(--art-mid) 0%, var(--art-dark) 100%);
    opacity: .92;
  }
  .card--back .brand-art {
    left: 0; top: 40px; width: 190px; height: 334px;
    border-radius: 0 60px 40px 0;
  }
  .card--front .brand-art {
    right: 0; top: 0; width: 260px; height: 250px;
    border-radius: 0 0 0 90px;
  }

  .brand {
    display: flex;
    flex-direction: column;
    align-items: center;
    gap: 10px;
  }
  .brand__dot {
    width: 62px; height: 62px;
    border-radius: 50%;
    background: var(--red);
  }
  .brand__name {
    font-family: "Audiowide", "Arial Black", sans-serif;
    color: var(--red);
    font-size: 30px;
    line-height: 1.05;
    text-align: center;
    letter-spacing: 1px;
  }

  .rule {
    width: 260px;
    height: 1px;
    background: var(--rule);
  }

  .back-content {
    position: absolute;
    left: 230px; right: 30px; top: 40px;
    display: flex;
    flex-direction: column;
    align-items: center;
    gap: 12px;
  }
  .services__title {
    font-family: "Arimo", Arial, sans-serif;
    font-weight: 700;
    font-size: 18px;
    color: var(--ink);
    letter-spacing: 1px;
  }
  .services__list {
    list-style: none;
    text-align: center;
    font-size: 15px;
    line-height: 1.55;
    color: var(--body);
  }

  .front-content {
    position: absolute;
    left: 60px; top: 60px; width: 380px;
    display: flex;
    flex-direction: column;
    align-items: center;
    gap: 12px;
  }
  .person__name {
    font-family: "Audiowide", "Arial Black", sans-serif;
    font-size: 28px;
    color: var(--ink);
    letter-spacing: 1px;
  }
  .person__role {
    font-size: 16px;
    color: var(--red);
    letter-spacing: 1px;
    margin-top: -10px;
  }
  .contact {
    list-style: none;
    font-size: 15px;
    color: var(--body);
    display: flex;
    flex-direction: column;
    align-items: center;
    gap: 8px;
    margin-top: 6px;
  }
  .contact__row { display: flex; align-items: center; gap: 8px; }
  .contact__sep { color: var(--ink); }
  .contact svg { width: 16px; height: 16px; flex: none; }
</style>
</head>
<body>

  <section class="card card--back" aria-label="Card back, services">
    <div class="brand-art" role="img" aria-label="Large brand illustration area"></div>
    <div class="back-content">
      <div class="brand">
        <div class="brand__dot"></div>
        <div class="brand__name">COPPERLEAF<br>ROOFING CO.</div>
      </div>
      <div class="rule"></div>
      <h2 class="services__title">SERVICES</h2>
      <div class="rule"></div>
      <ul class="services__list">
        <li>Residential &amp; Commercial Roofing / Roof Repairs &amp; Maintenance</li>
        <li>Storm Damage &amp; Insurance Claims Specialist</li>
        <li>Christmas Lights And Permanent Christmas Lights</li>
        <li>Fencing. Windows. Gutters. Siding. Sheetrock, painting.</li>
      </ul>
    </div>
    <div class="tartan-band"></div>
  </section>

  <section class="card card--front" aria-label="Card front, contact">
    <div class="brand-art" role="img" aria-label="Large brand illustration area"></div>
    <div class="front-content">
      <div class="brand">
        <div class="brand__dot"></div>
        <div class="brand__name">COPPERLEAF<br>ROOFING CO.</div>
      </div>
      <div class="rule"></div>
      <h1 class="person__name">DALE MERRICK</h1>
      <p class="person__role">OWNER</p>
      <div class="rule"></div>
      <ul class="contact">
        <li class="contact__row">
          <svg viewBox="0 0 24 24" aria-hidden="true"><path fill="#111" d="M6.6 10.8a15.1 15.1 0 0 0 6.6 6.6l2.2-2.2a1 1 0 0 1 1-.25 11.4 11.4 0 0 0 3.6.57 1 1 0 0 1 1 1V20a1 1 0 0 1-1 1A17 17 0 0 1 3 4a1 1 0 0 1 1-1h3.5a1 1 0 0 1 1 1c0 1.25.2 2.45.57 3.57a1 1 0 0 1-.25 1z"/></svg>
          <span>555-014-2283</span>
          <span class="contact__sep">|</span>
          <svg viewBox="0 0 24 24" aria-hidden="true"><rect x="2" y="5" width="20" height="14" fill="#111"/><path d="M2 5l10 8 10-8" fill="none" stroke="#fff" stroke-width="1.6"/></svg>
          <span>dale@copperleafroofing.co</span>
        </li>
        <li class="contact__row">
          <svg viewBox="0 0 24 24" aria-hidden="true"><g fill="none" stroke="#111" stroke-width="1.6"><circle cx="12" cy="12" r="9"/><ellipse cx="12" cy="12" rx="4" ry="9"/><path d="M3 12h18M5 7h14M5 17h14"/></g></svg>
          <span>www.copperleafroofing.co</span>
        </li>
      </ul>
    </div>
    <div class="tartan-band"></div>
  </section>

</body>
</html>
```